Document Processing Services and Solutions for School Systems

I am looking to design a brochure for both Digital and Paper use. I can supply the written content. Would be looking for an overall design of the brochure with provided content worked into it.

```html
<!DOCTYPE html>
<html lang="en">
<head>
<meta charset="utf-8">
<title>Northgate Systems Inc – School Document Management</title>
<link href="https://fonts.googleapis.com/css2?family=Poppins:ital,wght@0,300;0,400;0,500;0,600;1,500;1,600;1,700&display=swap" rel="stylesheet">
<style>
  :root{
    --indigo:#434586;
    --gold:#c9992a;
    --grey:#d5d5d8;
    --paper:#ffffff;
    --ink:#434586;
  }
  *{margin:0;padding:0;box-sizing:border-box}
  html,body{width:934px;height:1200px;overflow:hidden;background:var(--paper)}
  body{font-family:"Poppins",sans-serif;color:var(--ink);position:relative}
  .abs{position:absolute}

  /* header */
  .brand{left:62px;top:72px;width:330px;text-align:center}
  .brand-name{font-weight:600;font-size:24px;line-height:1.1;color:var(--indigo);display:flex;align-items:center;justify-content:center;gap:10px;white-space:nowrap}
  .brand-mark{width:13px;height:13px;background:var(--indigo);display:inline-block}
  .brand-rule{margin:14px auto 0;width:300px;height:1px;background:var(--gold)}
  .headline-band{left:428px;top:34px;width:506px;height:112px;background:var(--indigo);clip-path:polygon(5% 0,100% 0,100% 100%,0 100%)}
  .headline{left:455px;top:49px;width:470px;color:#fff;font-style:italic;font-weight:600;font-size:23px;line-height:26px;white-space:nowrap}
  .headline span{display:block}
  .headline .l1{padding-left:14px}
  .headline .l2{padding-left:5px}
  .tagline-band{left:0;top:146px;width:412px;height:32px;background:var(--gold);clip-path:polygon(0 0,100% 0,97% 100%,0 100%)}
  .tagline{left:60px;top:146px;line-height:32px;color:#fff;font-style:italic;font-weight:600;font-size:21px;white-space:nowrap}
  .intro{left:62px;top:156px;width:806px;font-style:italic;font-weight:500;font-size:11.6px;line-height:15px;text-align:justify}
  .intro-gap{float:left;width:372px;height:30px}

  .hero{left:0;top:228px;width:934px;height:278px;background:linear-gradient(120deg,#0c1f4e 0%,#1d5fa8 40%,#3bb2e0 55%,#1a4a93 75%,#0b1b45 100%)}

  /* services */
  .section-title{font-style:italic;font-weight:500;font-size:23px;letter-spacing:.5px;color:var(--indigo)}
  .services-title{left:0;width:934px;top:522px;text-align:center}
  .card{top:585px;width:262px;height:272px;border:2px solid var(--gold);border-radius:12px;background:#fff}
  .card::after{content:"";position:absolute;inset:3px;border:1px solid var(--indigo);border-radius:9px}
  .card-icon{position:absolute;left:50%;top:-21px;margin-left:-37px;width:74px;height:56px;z-index:2}
  .card-icon .back{position:absolute;left:4px;top:4px;width:70px;height:52px;background:var(--gold);transform:skewX(-10deg)}
  .card-icon .front{position:absolute;left:0;top:0;width:70px;height:52px;background:var(--indigo);border:2px solid #fff;outline:1px solid var(--gold);transform:skewX(-10deg);display:flex;align-items:center;justify-content:center}
  .card-icon svg{transform:skewX(10deg)}
  .card-title{position:absolute;left:12px;right:12px;top:46px;text-align:center;font-weight:400;font-size:16.5px;line-height:1.25;color:var(--indigo);z-index:1}
  .card-list{position:absolute;left:17px;right:14px;list-style:none;z-index:1}
  .card-list li{position:relative;padding-left:18px;font-weight:400;font-size:11.2px;line-height:1.3;margin-bottom:13px;color:var(--indigo)}
  .card-list li::before{content:"";position:absolute;left:0;top:3px;width:8px;height:7px;background:var(--indigo);transform:skewX(-15deg)}
  .card-list li::after{content:"";position:absolute;left:3px;top:7px;width:8px;height:6px;background:var(--gold);transform:skewX(-15deg)}

  /* why */
  .why-title{left:62px;top:872px;font-weight:600;font-size:23px}
  .why-band{left:0;top:927px;width:934px;height:152px;background:var(--grey)}
  .why-item{width:300px;height:52px}
  .why-icon{position:absolute;left:0;top:4px;width:54px;height:42px}
  .why-icon .back{position:absolute;left:5px;top:5px;width:48px;height:38px;background:var(--indigo);transform:skewX(-10deg)}
  .why-icon .front{position:absolute;left:0;top:0;width:48px;height:38px;background:var(--gold);transform:skewX(-10deg);display:flex;align-items:center;justify-content:center}
  .why-icon svg{transform:skewX(10deg)}
  .why-text{position:absolute;left:74px;top:-2px;white-space:nowrap}
  .why-head{font-weight:500;font-size:17.5px;line-height:20px;letter-spacing:.2px}
  .why-desc{font-weight:400;font-size:13.2px;line-height:15px}
  .student{left:690px;top:882px;width:220px;height:197px;border-radius:90px 90px 0 0;background:linear-gradient(180deg,#c9b8a5 0%,#8a8f9c 55%,#c79e6c 100%)}

  /* call to action */
  .cta-band{left:0;top:1096px;width:655px;height:67px;background:var(--indigo);clip-path:polygon(0 0,100% 0,96.5% 100%,0 100%)}
  .cta{left:62px;top:1104px;color:#fff;white-space:nowrap}
  .cta-head{font-style:italic;font-weight:700;font-size:17.5px;line-height:20px}
  .cta-body{font-weight:400;font-size:12.8px;line-height:15px}
  .contact-head{left:658px;top:1091px;width:210px;text-align:center;font-style:italic;font-weight:700;font-size:16.5px;line-height:19px;color:var(--indigo);white-space:nowrap}
  .phone-band{left:616px;top:1131px;width:182px;height:32px;left:652px;width:226px;background:var(--gold);clip-path:polygon(4% 0,100% 0,96% 100%,0 100%)}
  .phone{left:670px;top:1131px;line-height:32px;color:#fff;font-weight:500;font-size:21px;display:flex;align-items:center;gap:7px}
</style>
</head>
<body>

<header>
  <div class="abs brand">
    <div class="brand-name"><span class="brand-mark"></span>Northgate Systems Inc</div>
    <div class="brand-rule"></div>
  </div>
  <div class="abs headline-band"></div>
  <h1 class="abs headline">
    <span class="l1">Transform Your</span>
    <span class="l2">School’s Document Management</span>
    <span>with Our Comprehensive Solutions</span>
  </h1>
  <div class="abs tagline-band"></div>
  <p class="abs tagline">Streamline, Secure, &amp; Simplify</p>
  <p class="abs intro"><span class="intro-gap"></span>Managing school documents efficiently is crucial for smooth operations, compliance, and productivity. Our document processing services provide innovative solutions tailored for educational institutions, ensuring secure and seamless document and data handling.</p>
</header>

<div class="abs hero" role="img" aria-label="Three computer monitors in front of a night city skyline with glowing blue binary data streams"></div>

<section>
  <h2 class="abs section-title services-title">OUR SERVICES</h2>

  <article class="abs card" style="left:63px">
    <div class="card-icon"><div class="back"></div><div class="front">
      <svg width="26" height="26" viewBox="0 0 26 26" fill="none" stroke="#fff" stroke-width="1.4"><path d="M3 7V3h4M19 3h4v4M23 19v4h-4M7 23H3v-4"/><rect x="8" y="5" width="10" height="16"/><path d="M10 9h6M10 12h6M10 15h6M10 18h6M5 13h16"/></svg>
    </div></div>
    <h3 class="card-title">Document Scanning &amp; Conversion</h3>
    <ul class="card-list" style="top:104px">
      <li>Convert paper records into digital formats for easy access and storage.</li>
      <li>High-speed scanning for student records, administrative files, and historical archives.</li>
      <li>OCR (Optical Character Recognition) for searchable and editable documents.</li>
    </ul>
  </article>

  <article class="abs card" style="left:336px">
    <div class="card-icon"><div class="back"></div><div class="front">
      <svg width="32" height="26" viewBox="0 0 32 26" fill="none" stroke="#fff" stroke-width="1.4"><path d="M8 20a6 6 0 0 1 0-12 8 8 0 0 1 15-1 6 6 0 0 1 1 13z"/><path d="M14 19V10l-2 2M18 11v9l2-2"/></svg>
    </div></div>
    <h3 class="card-title">Cloud-Based Document Management</h3>
    <ul class="card-list" style="top:103px">
      <li>Secure, centralized document storage accessible from anywhere.</li>
      <li>Role-based access controls for administrators, teachers, and staff.</li>
      <li>Automated backups and compliance with educational data security standards.</li>
    </ul>
  </article>

  <article class="abs card" style="left:608px">
    <div class="card-icon"><div class="back"></div><div class="front">
      <svg width="32" height="32" viewBox="0 0 32 32" fill="none" stroke="#fff" stroke-width="1.4"><circle cx="9" cy="8" r="4" stroke-dasharray="2 1.2"/><circle cx="23" cy="14" r="4" stroke-dasharray="2 1.2"/><circle cx="9" cy="24" r="4" stroke-dasharray="2 1.2"/><path d="M15 7h6l-2-2M17 26h6v-4"/></svg>
    </div></div>
    <h3 class="card-title">Workflow Automation</h3>
    <ul class="card-list" style="top:103px">
      <li>Digitize and streamline approval processes for enrollment, transcripts, and HR forms.</li>
      <li>Reduce paperwork and improve efficiency with automated workflows.</li>
      <li>Integration capable with existing school management systems.</li>
    </ul>
  </article>
</section>

<section>
  <h2 class="abs section-title why-title">WHY CHOOSE US?</h2>
  <div class="abs why-band"></div>

  <div class="abs why-item" style="left:62px;top:947px">
    <div class="why-icon"><div class="back"></div><div class="front">
      <svg width="22" height="22" viewBox="0 0 22 22" fill="none" stroke="var(--indigo)" stroke-width="1.3"><circle cx="11" cy="11" r="6" stroke-dasharray="3 1.5"/><circle cx="11" cy="11" r="3"/></svg>
    </div></div>
    <div class="why-text"><div class="why-head">INCREASED EFFICIENCY</div><div class="why-desc">Save time with digital workflows<br>and instant document retrieval.</div></div>
  </div>

  <div class="abs why-item" style="left:388px;top:947px">
    <div class="why-icon"><div class="back"></div><div class="front">
      <svg width="20" height="22" viewBox="0 0 20 22" fill="none" stroke="var(--indigo)" stroke-width="1.3"><path d="M10 2l7 3v6c0 5-3 8-7 9-4-1-7-4-7-9V5z"/><path d="M6.5 11l2.5 2.5 4.5-5"/></svg>
    </div></div>
    <div class="why-text"><div class="why-head">ENHANCED SECURITY</div><div class="why-desc">Protect sensitive student<br>and faculty information.</div></div>
  </div>

  <div class="abs why-item" style="left:62px;top:1014px">
    <div class="why-icon"><div class="back"></div><div class="front">
      <svg width="22" height="22" viewBox="0 0 22 22" fill="none" stroke="var(--indigo)" stroke-width="1.3"><circle cx="11" cy="11" r="8"/><text x="11" y="15" text-anchor="middle" font-family="Poppins,sans-serif" font-size="11" fill="var(--indigo)" stroke="none">$</text></svg>
    </div></div>
    <div class="why-text"><div class="why-head">COST SAVINGS</div><div class="why-desc">Reduce paper, printing,<br>and storage costs.</div></div>
  </div>

  <div class="abs why-item" style="left:388px;top:1014px">
    <div class="why-icon"><div class="back"></div><div class="front">
      <svg width="22" height="22" viewBox="0 0 22 22" fill="none" stroke="var(--indigo)" stroke-width="1.3"><path d="M4 11a7 7 0 0 1 12-5M18 11a7 7 0 0 1-12 5"/><path d="M16 2v4h-4M6 20v-4h4"/></svg>
    </div></div>
    <div class="why-text"><div class="why-head">ECO-FRIENDLY</div><div class="why-desc">Minimize your school’s carbon<br>footprint by going digital.</div></div>
  </div>

  <div class="abs student" role="img" aria-label="Smiling young student writing at a wooden desk"></div>
</section>

<footer>
  <div class="abs cta-band"></div>
  <div class="abs cta">
    <p class="cta-head">GET STARTED TODAY!</p>
    <p class="cta-body">Let us help you modernize your document processing system.<br>Discover how our solutions can transform your school's document management.</p>
  </div>
  <p class="abs contact-head">CONTACT US FOR A<br>FREE CONSULTATION</p>
  <div class="abs phone-band"></div>
  <p class="abs phone">
    <svg width="15" height="15" viewBox="0 0 24 24" fill="#fff"><path d="M6.6 10.8a15 15 0 0 0 6.6 6.6l2.2-2.2a1 1 0 0 1 1-.25 11.4 11.4 0 0 0 3.6.57 1 1 0 0 1 1 1V20a1 1 0 0 1-1 1A17 17 0 0 1 3 4a1 1 0 0 1 1-1h3.5a1 1 0 0 1 1 1c0 1.25.2 2.45.57 3.57a1 1 0 0 1-.25 1z"/></svg>
    555-014-2290
  </p>
</footer>

</body>
</html>
```